Spring Detox sale graphics for social media

You MUST read the Brief in the WORD document and follow the instructions there. I want to create 10 social media graphics (new Instagram size 4:5 (1080 x 1350 pixels) focusing on our Mother’s Day Spring Detox Sale graphics, using any of the pics attached. Use the attached pics, NO RANDOM STOCK PHOTOGRAPHY. For the color scheme of the graphics, they should all be complementary to the product colors or feel like Spring time.

Target Market(s)

primarily women

Requirements
Must have
• the photos and text attached

```html
<!DOCTYPE html>
<html lang="en">
<head>
<meta charset="utf-8">
<title>Spring Detox Sale – Social Graphics</title>
<link rel="stylesheet" href="https://fonts.googleapis.com/css2?family=Oswald:wght@300;400;700&family=Montserrat:wght@600&display=swap">
<style>
  :root {
    --backdrop: #2b2b2b;
    --card: #ffffff;
    --frame: #efb3b8;
    --red: #bd2430;
    --ink: #2a2a2a;
    --light: #ffffff;
  }
  * { margin: 0; padding: 0; box-sizing: border-box; }
  html, body { width: 1200px; height: 3119px; overflow: hidden; background: var(--backdrop); }
  .board { position: relative; width: 1200px; height: 3119px; }

  .post {
    position: absolute; width: 460px; height: 575px;
    background: var(--card); overflow: hidden;
  }
  .post::before {
    content: ""; position: absolute; inset: 27px;
    border: 1.5px solid var(--frame); border-radius: 14px;
  }
  .col-left { left: 131px; }
  .col-right { left: 615px; }

  .copy { position: absolute; top: 0; bottom: 0; left: var(--x, 69px); width: var(--w, 321px); }
  .line {
    position: absolute; left: 0; width: 100%; top: var(--y);
    font-family: "Oswald", sans-serif; font-size: var(--fs);
    line-height: 1; white-space: nowrap; text-align: center; color: var(--ink);
  }
  .line > .fit {
    display: inline-block;
    transform: scaleX(var(--sx, 1));
    transform-origin: center top;
  }
  .align-start .line { text-align: left; }
  .align-start .line > .fit { transform-origin: left top; }
  .bold { font-weight: 700; letter-spacing: -0.01em; }
  .thin { font-weight: 300; }
  .regular { font-weight: 400; }
  .red { color: var(--red); }

  .banner { position: absolute; left: 0; width: 100%; top: var(--y); height: var(--h, 56px); }
  .banner svg { position: absolute; inset: 0; width: 100%; height: 100%; }
  .banner .label {
    position: absolute; inset: 0; display: flex; align-items: center; justify-content: center;
    font-family: "Montserrat", sans-serif; font-weight: 600; font-size: var(--fs, 40px);
    color: var(--light); line-height: 1;
  }

  .side-tag {
    position: absolute; left: var(--cx); top: var(--cy);
    transform: translate(-50%, -50%) rotate(-90deg) scaleX(var(--sx, 1));
    font-family: "Oswald", sans-serif; font-weight: 700; font-size: var(--fs);
    line-height: 1; white-space: nowrap; color: var(--ink);
  }
  .mix span.red { color: var(--red); }
</style>
</head>
<body>
<svg width="0" height="0" style="position:absolute">
  <defs>
    <symbol id="ribbon" viewBox="0 0 320 56" preserveAspectRatio="none">
      <polygon points="0,0 320,0 302,28 320,56 0,56 18,28" fill="#bd2430"/>
      <polyline points="26,5 42,28 26,51" fill="none" stroke="#ffffff" stroke-width="4"/>
      <polyline points="294,5 278,28 294,51" fill="none" stroke="#ffffff" stroke-width="4"/>
    </symbol>
  </defs>
</svg>

<main class="board">

  <!-- Post 1 -->
  <section class="post col-left" style="top:75px">
    <div class="copy">
      <p class="line bold red" style="--y:59px;--fs:64px;--sx:.97"><span class="fit">Mother’s Day</span></p>
      <p class="line thin" style="--y:114px;--fs:120px"><span class="fit">SPRING</span></p>
      <p class="line bold" style="--y:222px;--fs:128px"><span class="fit">DETOX</span></p>
      <div class="banner" style="--y:359px;--h:57px;--fs:44px">
        <svg><use href="#ribbon"/></svg><span class="label">25% OFF</span>
      </div>
      <p class="line regular" style="--y:421px;--fs:87px;--sx:.93"><span class="fit">Everything!</span></p>
    </div>
  </section>

  <!-- Post 2 -->
  <section class="post col-right" style="top:75px">
    <div class="copy" style="--x:70px;--w:317px">
      <p class="line bold red" style="--y:44px;--fs:98px;--sx:.88"><span class="fit">25% OFF</span></p>
      <p class="line bold" style="--y:139px;--fs:65px;--sx:.85"><span class="fit">MOTHER’S DAY</span></p>
      <p class="line thin red" style="--y:198px;--fs:120px;--sx:.98"><span class="fit">SPRING</span></p>
      <p class="line bold" style="--y:305px;--fs:133px;--sx:.96"><span class="fit">DETOX</span></p>
      <div class="banner" style="--y:443px;--h:55px;--fs:44px">
        <svg><use href="#ribbon"/></svg><span class="label">Sale</span>
      </div>
    </div>
  </section>

  <!-- Post 3 -->
  <section class="post col-left" style="top:680px">
    <div class="copy" style="--x:70px;--w:317px">
      <p class="line bold red" style="--y:50px;--fs:98px;--sx:.88"><span class="fit">25% OFF</span></p>
      <p class="line bold" style="--y:148px;--fs:53px;--sx:.81"><span class="fit">ALL SUPPLEMENTS</span></p>
      <p class="line thin red" style="--y:199px;--fs:120px;--sx:.98"><span class="fit">SPRING</span></p>
      <p class="line bold" style="--y:308px;--fs:133px;--sx:.96"><span class="fit">DETOX</span></p>
      <div class="banner" style="--y:453px;--h:55px;--fs:44px">
        <svg><use href="#ribbon"/></svg><span class="label">Sale!</span>
      </div>
    </div>
  </section>

  <!-- Post 4 -->
  <section class="post col-right" style="top:680px">
    <div class="copy align-start" style="--x:42px;--w:321px">
      <p class="line bold red" style="--y:47px;--fs:98px;--sx:.88"><span class="fit">25% OFF</span></p>
      <p class="line thin" style="--y:136px;--fs:120px;--sx:.98"><span class="fit">SPRING</span></p>
      <p class="line bold" style="--y:245px;--fs:133px;--sx:.96"><span class="fit">DETOX</span></p>
      <div class="banner" style="--y:388px;--h:55px;--fs:44px">
        <svg><use href="#ribbon"/></svg><span class="label">Sale</span>
      </div>
      <p class="line thin" style="--y:447px;--fs:78px;--sx:.94"><span class="fit">Spring Reset</span></p>
    </div>
    <p class="side-tag" style="--cx:405px;--cy:289px;--fs:66px;--sx:1.08">SUMMER READY</p>
  </section>

  <!-- Post 5 -->
  <section class="post col-left" style="top:1286px">
    <div class="copy" style="--x:70px;--w:317px">
      <p class="line bold red" style="--y:32px;--fs:98px;--sx:.88"><span class="fit">25% OFF</span></p>
      <p class="line thin" style="--y:122px;--fs:76px;--sx:.93"><span class="fit">EVERYTHING</span></p>
      <p class="line bold red" style="--y:195px;--fs:60px;--sx:1.02"><span class="fit">Mother’s Day</span></p>
      <p class="line thin" style="--y:250px;--fs:118px;--sx:.98"><span class="fit">SPRING</span></p>
      <p class="line bold" style="--y:356px;--fs:133px;--sx:.96"><span class="fit">DETOX</span></p>
      <div class="banner" style="--y:496px;--h:53px;--fs:44px">
        <svg><use href="#ribbon"/></svg><span class="label">Sale</span>
      </div>
    </div>
  </section>

  <!-- Post 6 -->
  <section class="post col-right" style="top:1286px">
    <div class="copy" style="--x:57px;--w:349px">
      <p class="line bold red" style="--y:55px;--fs:106px;--sx:.89"><span class="fit">25% OFF</span></p>
      <p class="line bold" style="--y:159px;--fs:70px;--sx:.87"><span class="fit">MOTHER’S DAY</span></p>
      <div class="banner" style="--y:237px;--h:57px;--fs:46px">
        <svg><use href="#ribbon"/></svg><span class="label">Sale</span>
      </div>
      <p class="line thin" style="--y:302px;--fs:76px;--sx:.92"><span class="fit">FEEL AMAZING</span></p>
      <p class="line bold" style="--y:372px;--fs:141px;--sx:.93"><span class="fit">AGAIN!</span></p>
    </div>
  </section>

  <!-- Post 7 -->
  <section class="post col-left" style="top:1891px">
    <div class="copy" style="--x:53px;--w:351px">
      <p class="line bold red" style="--y:43px;--fs:106px;--sx:.89"><span class="fit">25% OFF</span></p>
      <p class="line bold" style="--y:147px;--fs:72px;--sx:.85"><span class="fit">MOTHER’S DAY</span></p>
      <div class="banner" style="--y:226px;--h:57px;--fs:46px">
        <svg><use href="#ribbon"/></svg><span class="label">Sale</span>
      </div>
      <p class="line thin" style="--y:305px;--fs:70px;--sx:.92"><span class="fit">REFRESH YOUR</span></p>
      <p class="line bold" style="--y:360px;--fs:162px"><span class="fit">BODY</span></p>
    </div>
  </section>

  <!-- Post 8 -->
  <section class="post col-right" style="top:1891px">
    <div class="copy align-start" style="--x:40px;--w:320px">
      <p class="line bold red" style="--y:47px;--fs:98px;--sx:.88"><span class="fit">25% OFF</span></p>
      <p class="line thin" style="--y:138px;--fs:120px;--sx:.98"><span class="fit">SPRING</span></p>
      <p class="line bold" style="--y:248px;--fs:133px;--sx:.96"><span class="fit">DETOX</span></p>
      <div class="banner" style="--y:391px;--h:55px;--fs:44px">
        <svg><use href="#ribbon"/></svg><span class="label">Sale</span>
      </div>
      <p class="line thin" style="--y:448px;--fs:72px;--sx:.88"><span class="fit">Spring Cleanse</span></p>
    </div>
    <p class="side-tag" style="--cx:405px;--cy:285px;--fs:66px;--sx:1.08">SUMMER GLOW</p>
  </section>

  <!-- Post 9 -->
  <section class="post col-left" style="top:2497px">
    <div class="copy align-start" style="--x:41px;--w:320px">
      <p class="line bold red" style="--y:68px;--fs:100px;--sx:.86"><span class="fit">25% OFF</span></p>
      <p class="line bold" style="--y:161px;--fs:64px;--sx:.85"><span class="fit">MOTHER’S DAY</span></p>
      <div class="banner" style="--y:237px;--h:53px;--fs:42px">
        <svg><use href="#ribbon"/></svg><span class="label">Sale</span>
      </div>
      <p class="line thin" style="--y:290px;--fs:90px;--sx:.98"><span class="fit">Detox This</span></p>
      <p class="line bold" style="--y:379px;--fs:121px;--sx:.89"><span class="fit">SPRING</span></p>
    </div>
    <p class="side-tag mix" style="--cx:398px;--cy:288px;--fs:54px;--sx:.93"><span class="red">SHINE THIS</span> SUMMER</p>
  </section>

  <!-- Post 10 -->
  <section class="post col-right" style="top:2497px">
    <div class="copy" style="--x:70px;--w:317px">
      <p class="line bold red" style="--y:30px;--fs:98px;--sx:.88"><span class="fit">25% OFF</span></p>
      <p class="line bold" style="--y:128px;--fs:65px;--sx:.85"><span class="fit">MOTHER’S DAY</span></p>
      <div class="banner" style="--y:200px;--h:55px;--fs:44px">
        <svg><use href="#ribbon"/></svg><span class="label">Sale</span>
      </div>
      <p class="line thin" style="--y:254px;--fs:120px;--sx:.98"><span class="fit">SPRING</span></p>
      <p class="line bold" style="--y:360px;--fs:133px;--sx:.96"><span class="fit">DETOX</span></p>
      <p class="line thin mix" style="--y:489px;--fs:52px;--sx:.84"><span class="fit">for a <span class="bold red">Summer Body</span></span></p>
    </div>
  </section>

</main>
</body>
</html>
```